Flyer to promote an IT Innovation Fest

BWL Spark Summit 2018

We are looking to implement a new Innovation program that uses the Morvane LaunchCrate concept. Team Members will receive a red box that contains a set of 20 flash cards that help them to bring an innovative idea to life (based on a business problem or friction point).
We are looking to create a cover page for our 'Red Box' via way of a 1 page flyer.
We want to call it the 'BWL Spark Summit 2018'. We would like the 1 page flyer to look super cool and also have some kind of cool cartoon imagery to bring it to life.
We also want to incorporate our logo into the page somewhere as well.

Ideally, we'd also like to get a logo called 'Spark Summit' that we could use on some of our collateral as well. I thought it might be best to create the 1 pager flyer first, then we could look to pull a Spark Summit logo off that. Please let me know though whether it would be easier to create the logo first, then create the flyer).

Bluewater Labs are a support business to Bluewater Journeys Group which is the largest travel retailer in Australia. Our IT area has around 150 permanent team members. We have a fun culture and can push the boundaries with our imagery as the flyer will be for internal distribution only.

I have attached the Morvane Flash cards that this 1 pager will be the cover page for.

Target Market(s)

Members of the Bluewater Labs team (internal marketing)

Industry/Entity Type

It Company

Requirements
Must have
• Our BWL Logo
• A super cool, innovative, funky look (with some kind of cartoon imagery)
• We need to be able to edit the flyer to add some text
Nice to have
• Stay within the colour theme of the 'Start Here' page on the Morvane attachment

```html
<!DOCTYPE html>
<html lang="en">
<head>
<meta charset="utf-8">
<title>BWL Spark Summit 2018 – Flyer</title>
<link rel="stylesheet" href="https://fonts.googleapis.com/css2?family=Montserrat:wght@100;300;700;800;900&family=Oswald:wght@700&display=swap">
<style>
  :root {
    --page-bg: #e6e6e6;
    --flyer-red: #a51b2b;
    --flyer-red-deep: #8f1523;
    --flyer-red-light: #b8202f;
    --accent-red: #e8202a;
    --ink: #141414;
    --paper: #ffffff;
    --bulb-tone: #f2f2f2;
  }
  html, body {
    margin: 0;
    padding: 0;
    width: 1200px;
    height: 1200px;
    overflow: hidden;
    background: var(--page-bg);
  }
  .flyer {
    position: absolute;
    left: 196px;
    top: 30px;
    width: 844px;
    height: 1190px;
    transform: scale(0.958);
    transform-origin: top left;
    background: var(--paper);
    box-shadow: 0 6px 24px rgba(0,0,0,0.25);
    overflow: hidden;
  }
  .flyer__stage {
    position: absolute;
    left: 0; top: 0;
    width: 844px;
    height: 1010px;
    background:
      linear-gradient(150deg, var(--flyer-red-light) 0%, var(--flyer-red) 40%, var(--flyer-red-deep) 70%, var(--flyer-red) 100%);
  }
  .flyer__frame {
    position: absolute;
    left: 19px; top: 15px;
    width: 808px;
    height: 995px;
    border: 1.5px solid rgba(255,255,255,0.85);
    border-bottom: none;
    box-sizing: border-box;
  }
  .mascot-art {
    position: absolute;
    left: 72px; top: 110px;
    width: 205px; height: 735px;
    border-radius: 100px 100px 40px 40px;
    background: linear-gradient(180deg, rgba(255,255,255,0.18) 0%, rgba(242,242,242,0.35) 55%, rgba(255,255,255,0.06) 100%);
  }
  .headline {
    position: absolute;
    left: 0; top: 0;
    width: 844px; height: 1010px;
  }
  .headline__brand {
    font-family: "Montserrat", sans-serif;
    font-weight: 900;
    fill: var(--ink);
    stroke: var(--paper);
    stroke-width: 7px;
    paint-order: stroke;
  }
  .headline__spark {
    font-family: "Oswald", sans-serif;
    font-weight: 700;
    fill: var(--paper);
  }
  .headline__summit {
    font-family: "Montserrat", sans-serif;
    font-weight: 100;
    fill: var(--paper);
  }
  .headline__year-box { fill: var(--accent-red); }
  .headline__year {
    font-family: "Montserrat", sans-serif;
    font-weight: 900;
    fill: #f4f4f4;
  }
  .flyer__footer {
    position: absolute;
    left: 0; top: 1010px;
    width: 844px; height: 180px;
    background: var(--paper);
  }
  .company {
    position: absolute;
    left: 62px; top: 30px;
    width: 210px;
    text-align: center;
  }
  .company__mark {
    display: block;
    width: 72px; height: 72px;
    margin: 0 auto 12px;
    border-radius: 50%;
    border: 4px solid var(--ink);
    box-sizing: border-box;
  }
  .company__name {
    font-family: "Montserrat", sans-serif;
    font-weight: 700;
    font-size: 21px;
    color: var(--accent-red);
    letter-spacing: 0.5px;
  }
  .contact {
    position: absolute;
    right: 60px; top: 52px;
    text-align: right;
    font-family: "Montserrat", sans-serif;
  }
  .contact__label {
    font-weight: 300;
    font-size: 30px;
    color: var(--accent-red);
    line-height: 1;
    margin-bottom: 12px;
  }
  .contact__phone {
    font-weight: 800;
    font-size: 54px;
    color: var(--ink);
    line-height: 1;
    letter-spacing: -1px;
  }
</style>
</head>
<body>
  <main class="flyer">
    <section class="flyer__stage">
      <div class="flyer__frame"></div>
      <div class="mascot-art" role="img" aria-label="Cartoon office worker in shirt and tie riding a white light bulb that launches upward like a rocket"></div>
      <svg class="headline" viewBox="0 0 844 1010" aria-label="BWL Spark Summit 2018">
        <text class="headline__brand" x="337" y="305" font-size="226" textLength="450" lengthAdjust="spacingAndGlyphs">BWL</text>
        <text class="headline__spark" x="337" y="440" font-size="150" textLength="448" lengthAdjust="spacing">SPARK</text>
        <text class="headline__summit" x="337" y="597" font-size="184" textLength="446" lengthAdjust="spacingAndGlyphs">SUMMIT</text>
        <rect class="headline__year-box" x="340" y="623" width="442" height="165"/>
        <text class="headline__year" x="561" y="765" font-size="162" text-anchor="middle" textLength="388" lengthAdjust="spacingAndGlyphs">2018</text>
      </svg>
    </section>
    <footer class="flyer__footer">
      <div class="company">
        <span class="company__mark"></span>
        <span class="company__name">BLUEWATER LABS</span>
      </div>
      <div class="contact">
        <div class="contact__label">Call Us Now</div>
        <div class="contact__phone">61 7 3000 4182</div>
      </div>
    </footer>
  </main>
</body>
</html>
```